Hacienda Monte Verda Business cards

We would like 3 individual business cards with the logo you designed:

1) Marta Pellingford - Phone: 425 555 0147
2) Theodore R Pellingford - Phone 206 555 0183
3) Dana Moreth - Phone 310-555-0162

Address for all three cards:
7218 142nd Ave NE
Fernhollow, WA 98561
HaciendaMonteVerda@brindlemail.com

```html
<!DOCTYPE html>
<html lang="en">
<head>
<meta charset="utf-8">
<title>Hacienda Monte Verda – Business Card</title>
<link rel="stylesheet" href="https://fonts.googleapis.com/css2?family=Montserrat:wght@400;700&display=swap">
<style>
  :root {
    --backdrop: #e4e4e2;
    --card-top: #ffffff;
    --card-bottom: #e9e9e9;
    --ink: #1a1a1a;
    --ink-soft: #2c2c2c;
    --shadow: rgba(0, 0, 0, 0.22);
  }
  html, body {
    margin: 0;
    padding: 0;
    width: 1200px;
    height: 871px;
    overflow: hidden;
    background: var(--backdrop);
  }
  .canvas {
    position: relative;
    width: 1200px;
    height: 871px;
    display: flex;
    align-items: center;
    justify-content: center;
  }
  .business-card {
    position: relative;
    width: 910px;
    height: 520px;
    background: linear-gradient(160deg, var(--card-top) 35%, var(--card-bottom) 100%);
    box-shadow: 0 14px 34px var(--shadow);
    font-family: "Montserrat", sans-serif;
    color: var(--ink);
  }
  .contact {
    position: absolute;
    left: 92px;
    top: 128px;
  }
  .contact__name {
    margin: 0 0 36px;
    font-size: 24px;
    font-weight: 700;
    letter-spacing: 0.2px;
  }
  .contact__row {
    display: flex;
    align-items: flex-start;
    margin-bottom: 20px;
    font-size: 15px;
    line-height: 1.75;
    color: var(--ink-soft);
  }
  .contact__icon {
    flex: none;
    width: 18px;
    height: 18px;
    margin: 4px 22px 0 0;
  }
  .contact__row p { margin: 0; }
  .brand {
    position: absolute;
    right: 70px;
    top: 270px;
    width: 380px;
    display: flex;
    align-items: center;
    justify-content: center;
    gap: 16px;
  }
  .brand__dot {
    flex: none;
    width: 18px;
    height: 18px;
    border-radius: 50%;
    background: var(--ink);
  }
  .brand__name {
    margin: 0;
    font-size: 36px;
    font-weight: 400;
    line-height: 1.2;
    letter-spacing: 1px;
    color: var(--ink);
    text-align: left;
  }
</style>
</head>
<body>
<main class="canvas">
  <article class="business-card">
    <section class="contact">
      <h1 class="contact__name">Marta Pellingford</h1>

      <div class="contact__row">
        <svg class="contact__icon" viewBox="0 0 18 18" aria-hidden="true">
          <rect x="4.5" y="1" width="9" height="16" rx="1.8" fill="none" stroke="currentColor" stroke-width="1.4"/>
          <line x1="7.5" y1="14.3" x2="10.5" y2="14.3" stroke="currentColor" stroke-width="1.2"/>
        </svg>
        <p>425 555 0147</p>
      </div>

      <div class="contact__row">
        <svg class="contact__icon" viewBox="0 0 18 18" aria-hidden="true">
          <path d="M9 17s-5.5-6-5.5-9.6a5.5 5.5 0 0 1 11 0C14.5 11 9 17 9 17z" fill="none" stroke="currentColor" stroke-width="1.4"/>
          <circle cx="9" cy="7.3" r="1.9" fill="none" stroke="currentColor" stroke-width="1.3"/>
        </svg>
        <p>Address for all three cards:<br>7218 142nd Ave NE<br>Fernhollow, WA 98561</p>
      </div>

      <div class="contact__row">
        <svg class="contact__icon" viewBox="0 0 18 18" aria-hidden="true">
          <rect x="1.5" y="4" width="15" height="10.5" fill="none" stroke="currentColor" stroke-width="1.4"/>
          <polyline points="1.5,4 9,10 16.5,4" fill="none" stroke="currentColor" stroke-width="1.3"/>
        </svg>
        <p>HaciendaMonteVerda@brindlemail.com</p>
      </div>
    </section>

    <div class="brand">
      <span class="brand__dot" aria-hidden="true"></span>
      <p class="brand__name">Hacienda<br>Monte Verda</p>
    </div>
  </article>
</main>
</body>
</html>
```